brqnal new business card design project

we need a new business card design. you can view info about us @ brqnal-example.com. i have attached an example of our previous card with our previous name that we no longer use. We really liked the design, colors etc. look below to see more info about this project. it asks for a limited number of words. please see our website for more info about our compnay.

Target Market(s)

law enforcement

Contact Information for Business Card

i have uploaded an example of what we used before that we liked.

Font styles to use
Serif

```html
<!DOCTYPE html>
<html lang="en">
<head>
<meta charset="utf-8">
<title>brqnal business card</title>
<link rel="stylesheet" href="https://fonts.googleapis.com/css2?family=Exo+2:wght@400&family=Roboto:ital,wght@0,100;0,300;0,400;1,400&display=swap">
<style>
  :root {
    --backdrop: #c8c8c8;
    --card-navy: #0b1824;
    --card-navy-deep: #07121c;
    --brand-blue: #0a7fc4;
    --band-blue: #0f65a0;
    --band-white: #e4e6e8;
    --text-light: #e8ecf0;
    --text-muted: #c9d2da;
  }
  * { box-sizing: border-box; margin: 0; padding: 0; }
  html, body { width: 1200px; height: 576px; overflow: hidden; }
  body {
    background: var(--backdrop);
    position: relative;
    font-family: "Roboto", Arial, sans-serif;
  }
  .card {
    position: absolute;
    top: 138px;
    width: 484px;
    height: 294px;
    border-radius: 14px;
    background: var(--card-navy);
    overflow: hidden;
    color: var(--text-light);
  }
  .card--front { left: 82px; }
  .card--back { left: 602px; width: 480px; height: 291px; background: var(--card-navy-deep); }

  .network-map {
    position: absolute;
    left: 24px; top: 30px;
    width: 440px; height: 230px;
    background: radial-gradient(ellipse at 50% 50%, rgba(40,70,90,0.35), rgba(11,24,36,0) 70%);
  }
  .wordmark {
    position: absolute;
    font-family: "Roboto", Arial, sans-serif;
    font-weight: 300;
    color: var(--text-light);
    letter-spacing: 0.08em;
    line-height: 1;
    white-space: nowrap;
  }
  .card--front .wordmark { left: 110px; top: 98px; font-size: 48px; }
  .card--back .wordmark { left: 34px; top: 113px; font-size: 39px; }

  .bottom-bands { position: absolute; left: 0; bottom: 0; }
  .card--front .bottom-bands { width: 280px; height: 23px; }
  .card--back .bottom-bands { width: 230px; height: 22px; }
  .band-blue { fill: var(--band-blue); }
  .band-white { fill: var(--band-white); }

  .site-url {
    position: absolute;
    right: 24px; bottom: 7px;
    font-size: 11.5px;
    letter-spacing: 0.1em;
    color: var(--text-muted);
    white-space: nowrap;
  }

  .contact { position: absolute; left: 292px; top: 62px; }
  .contact-name {
    font-family: "Exo 2", Arial, sans-serif;
    font-weight: 400;
    font-size: 21px;
    color: var(--brand-blue);
    line-height: 1.2;
  }
  .contact-title {
    font-style: italic;
    font-size: 12.5px;
    color: var(--text-muted);
    margin-top: 1px;
  }
  .contact-address {
    font-size: 13px;
    line-height: 17px;
    color: var(--text-muted);
    margin-top: 14px;
  }
  .contact-lines { list-style: none; margin-top: 7px; }
  .contact-lines li {
    display: flex; align-items: center;
    font-size: 13px; line-height: 17px;
    color: var(--text-muted);
  }
  .contact-lines svg { width: 11px; height: 11px; margin: 0 11px 0 2px; fill: var(--brand-blue); }

  .tagline {
    position: absolute;
    left: 250px; bottom: 8px;
    font-size: 12.5px;
    color: var(--text-muted);
    white-space: nowrap;
  }
  .tagline .divider { margin: 0 9px; }
</style>
</head>
<body>

<section class="card card--front">
  <div class="network-map" role="img" aria-label="Faint connected-dot network map of the country"></div>
  <div class="wordmark">BRQNAL</div>
  <svg class="bottom-bands" viewBox="0 0 280 23" aria-hidden="true">
    <polygon class="band-blue" points="0,0 192,0 182,23 0,23"/>
    <polygon class="band-white" points="210,0 270,0 258,23 198,23"/>
  </svg>
  <div class="site-url">www.brqnal-example.com</div>
</section>

<section class="card card--back">
  <div class="wordmark">BRQNAL</div>
  <div class="contact">
    <h1 class="contact-name">Dana Whitcomb</h1>
    <p class="contact-title">Founder/Chief Exe. Officer</p>
    <p class="contact-address">4120 Larkspur Lane<br>Austin, TX 78701</p>
    <ul class="contact-lines">
      <li><svg viewBox="0 0 12 12" aria-hidden="true"><path d="M1 4 Q6 0 11 4 L9.5 5.5 L8 4.5 L8 3.5 Q6 3 4 3.5 L4 4.5 L2.5 5.5 Z M3 6 L9 6 L10 11 L2 11 Z"/></svg>555.014.2290</li>
      <li><svg viewBox="0 0 12 12" aria-hidden="true"><path d="M0 2.5 H12 V10 H0 Z M0.8 3.2 L6 7 L11.2 3.2 L11.2 9.3 L0.8 9.3 Z" fill-rule="evenodd"/><path d="M0.8 3.2 L6 7 L11.2 3.2 L11.2 3.6 L6 7.5 L0.8 3.6 Z"/></svg>info@brqnal-example.com</li>
      <li><svg viewBox="0 0 12 12" aria-hidden="true"><path d="M6 0.5 A5.5 5.5 0 1 0 6 11.5 A5.5 5.5 0 1 0 6 0.5 Z M6 1.5 A4.5 4.5 0 1 1 6 10.5 A4.5 4.5 0 1 1 6 1.5 Z M5.5 1 H6.5 V11 H5.5 Z M1 5.5 H11 V6.5 H1 Z" fill-rule="evenodd"/></svg>www.brqnal-example.com</li>
    </ul>
  </div>
  <svg class="bottom-bands" viewBox="0 0 230 22" aria-hidden="true">
    <polygon class="band-blue" points="0,0 140,0 130,22 0,22"/>
    <polygon class="band-white" points="160,0 220,0 208,22 148,22"/>
  </svg>
  <p class="tagline">Better Technology<span class="divider">|</span>Better Service</p>
</section>

</body>
</html>
```